Timber Crest Construction Needs business card

Hey we are in need of business card designs. I have upload our logo as a guideline, but free feel to run with it or come up with something unique.
Pls have fun with it and be creative. the name says it all!
i will give some directions after i see a few entries..
Updates
Logo source file has been uploaded..
Hey because of the logo is so colourful already.
Can we have a few submissions with less colour.
Also we are looking for clever/hidden/descriptive business card.

```html
<!DOCTYPE html>
<html lang="en">
<head>
<meta charset="utf-8">
<title>Timber Crest Construction – Business Card</title>
<link href="https://fonts.googleapis.com/css2?family=Didact+Gothic&family=Montserrat:wght@700&display=swap" rel="stylesheet">
<style>
  :root {
    --stage: #1f7d02;
    --card: #ffffff;
    --band: #3a3a3c;
    --ink: #2b2b2b;
    --brand-grey: #7a7b7e;
    --accent: #e0262c;
    --faint: #e2e2e2;
  }
  * { margin: 0; padding: 0; box-sizing: border-box; }
  html, body { width: 1200px; height: 1200px; overflow: hidden; }
  body {
    position: relative;
    background: var(--stage);
    font-family: "Didact Gothic", "Century Gothic", sans-serif;
    color: var(--ink);
  }
  .card {
    position: absolute;
    width: 800px;
    height: 445px;
    background: var(--card);
    overflow: hidden;
  }
  .card--front { left: 212px; top: 130px; }
  .card--back { left: 220px; top: 649px; }

  .brand-name {
    font-family: "Didact Gothic", "Century Gothic", sans-serif;
    color: var(--brand-grey);
    white-space: nowrap;
  }
  .card--front .brand {
    position: absolute;
    left: 0; right: 0; top: 195px;
    display: flex; justify-content: center; align-items: center; gap: 16px;
  }
  .card--front .brand-mark { width: 34px; height: 34px; background: var(--brand-grey); }
  .card--front .brand-name { font-size: 38px; letter-spacing: 1px; }

  .band { position: absolute; left: 0; top: 0; width: 73px; height: 100%; background: var(--band); }

  .card--back .brand {
    position: absolute; left: 138px; top: 92px;
    display: flex; align-items: center; gap: 12px;
  }
  .card--back .brand-mark { width: 22px; height: 22px; background: var(--brand-grey); }
  .card--back .brand-name { font-size: 25px; letter-spacing: 0.5px; }

  .person { position: absolute; right: 89px; top: 119px; text-align: right; }
  .person-name {
    font-family: "Montserrat", "Arial", sans-serif;
    font-weight: 700; font-size: 15px; letter-spacing: 4px; color: #111;
  }
  .person-role { font-size: 14px; letter-spacing: 2.5px; color: var(--accent); margin-top: 6px; }

  .address {
    position: absolute; left: 137px; top: 214px;
    font-size: 14px; letter-spacing: 2.6px; line-height: 21px; text-transform: uppercase;
  }
  .contacts { position: absolute; left: 137px; top: 292px; list-style: none; }
  .contacts li {
    display: flex; align-items: center; height: 25px;
    font-size: 14px; letter-spacing: 2.4px;
  }
  .contacts svg { width: 15px; height: 15px; margin-right: 22px; flex: none; }

  .decor {
    position: absolute; right: 0; bottom: 0; width: 255px; height: 226px;
    background: linear-gradient(160deg, #ffffff 0%, var(--faint) 45%, #d6d6d6 100%);
  }
</style>
</head>
<body>
  <section class="card card--front">
    <div class="brand">
      <span class="brand-mark"></span>
      <span class="brand-name">Timber Crest Construction</span>
    </div>
  </section>

  <section class="card card--back">
    <div class="band"></div>
    <div class="brand">
      <span class="brand-mark"></span>
      <span class="brand-name">Timber Crest Construction</span>
    </div>

    <div class="person">
      <p class="person-name">MARLA VENN</p>
      <p class="person-role">DIRECTOR</p>
    </div>

    <p class="address">Shop 2, 318-322 Harbour<br>Road Westfield North</p>

    <ul class="contacts">
      <li>
        <svg viewBox="0 0 16 16" aria-hidden="true"><path fill="#e0262c" d="M2 5c0-2 2-3 6-3s6 1 6 3v1h-3V5H5v1H2zM4 7h8l2 6H2zM8 8.5a2 2 0 1 0 0 4 2 2 0 0 0 0-4z"/></svg>
        9315 2740
      </li>
      <li>
        <svg viewBox="0 0 16 16" aria-hidden="true"><g fill="none" stroke="#e0262c" stroke-width="1.6"><rect x="4" y="1.5" width="8" height="4"/><rect x="1.5" y="5.5" width="13" height="6"/><rect x="4" y="9.5" width="8" height="5"/></g></svg>
        9315 2781
      </li>
      <li>
        <svg viewBox="0 0 16 16" aria-hidden="true"><g fill="none" stroke="#e0262c" stroke-width="1.6"><rect x="1.5" y="3.5" width="13" height="9"/><path d="M1.5 3.5 8 9l6.5-5.5"/></g></svg>
        marla@timbercrestbuild.com
      </li>
      <li>
        <svg viewBox="0 0 16 16" aria-hidden="true"><g fill="none" stroke="#e0262c" stroke-width="1.5"><circle cx="8" cy="8" r="6.2"/><ellipse cx="8" cy="8" rx="2.8" ry="6.2"/><path d="M1.8 8h12.4M3 4.5h10M3 11.5h10"/></g></svg>
        www.timbercrestbuild.com
      </li>
    </ul>

    <div class="decor" role="img" aria-label="Faint grey building facade decoration"></div>
  </section>
</body>
</html>
```